Book Title: The Weaver's Lantern. Author Name: Maribel Trowcastle

We are needing a cover, spine and back cover design for a poetry book that we are publishing called The Weaver's Lantern. We are looking for an elegant, and simplistic design with a very natural, dynamic and powerful impact.

Design Idea #1 - Shiva Conch Shell with a pink or black background. See Paul Renwick Image attached for design inspiration. Simple and dynamic .
Title and Author name created in same style as the attached Paul Renwick's Harbors and Lanterns image.

Design Idea #2 - Image of cauldron on (see cauldrons attached for ideas) black background.
See Paul Renwick Image attached for design inspiration. Simple and dynamic Title and Author name created in same style as the attached Paul Renwick's Harbors and Lanterns image

Design Idea #3 - Image of Tree of Life (see attached images for idea of what we are looking for) Would like to see on plain white, green, black and green background.

Target Market(s)

Spiritual Women, healers, visionaries,Goddess'

Requirements
Must have
• Please see project descriptions for specific design concepts we are looking for. Please include the authors name: Maribel Trowcastle on front, spine and back cover of the book

```html
<!DOCTYPE html>
<html lang="en">
<head>
<meta charset="utf-8">
<title>The Weaver's Lantern — Cover Wrap</title>
<link href="https://fonts.googleapis.com/css2?family=EB+Garamond:wght@400;500&display=swap" rel="stylesheet">
<style>
  :root {
    --stage: #0e0e0e;
    --ink: #ffffff;
    --ink-soft: rgba(255,255,255,0.92);
    --magenta: #ff0a8c;
    --hot-pink: #ff3d6e;
    --violet: #8a2fd0;
    --indigo: #2a10d8;
    --amber: #c9a04a;
    --coral: #ee7a55;
    --mint: #4fe09a;
    --cyan: #16d8e0;
    --sky: #3ae6f5;
    --pearl: #f4f2f4;
    --pearl-shade: #d9c3bf;
  }
  * { margin: 0; padding: 0; box-sizing: border-box; }
  html, body {
    width: 1200px; height: 1200px; overflow: hidden;
    background: var(--stage);
  }
  .cover-wrap {
    position: absolute; left: 40px; top: 215px;
    width: 1120px; height: 770px;
    overflow: hidden;
    font-family: "EB Garamond", Georgia, serif;
    color: var(--ink);
    background:
      radial-gradient(ellipse 420px 360px at 0% 100%, var(--sky) 0%, rgba(22,216,224,0.85) 40%, rgba(22,216,224,0) 100%),
      radial-gradient(ellipse 360px 300px at 0% 55%, var(--mint) 0%, rgba(79,224,154,0) 100%),
      radial-gradient(ellipse 420px 260px at 0% 0%, var(--amber) 0%, rgba(201,160,74,0) 100%),
      radial-gradient(ellipse 380px 260px at 30% 0%, var(--coral) 0%, rgba(238,122,85,0) 100%),
      radial-gradient(ellipse 520px 380px at 100% 100%, var(--indigo) 0%, rgba(42,16,216,0.6) 35%, rgba(42,16,216,0) 100%),
      radial-gradient(ellipse 560px 380px at 70% 90%, var(--violet) 0%, rgba(138,47,208,0) 100%),
      radial-gradient(ellipse 620px 520px at 85% 25%, var(--magenta) 0%, rgba(255,10,140,0) 100%),
      linear-gradient(135deg, var(--coral) 0%, var(--hot-pink) 45%, var(--magenta) 70%, var(--violet) 100%);
  }

  /* Back cover */
  .back-cover {
    position: absolute; left: 47px; top: 0; width: 420px;
  }
  .back-title {
    position: absolute; top: 70px; left: 0; width: 420px;
    text-align: center;
    font-size: 27px; font-weight: 400; letter-spacing: 0.12em;
    text-transform: uppercase;
  }
  .back-blurb {
    position: absolute; top: 128px; left: 0; width: 420px;
  }
  .back-blurb p {
    font-size: 13.6px; line-height: 21.4px;
    text-align: justify; text-align-last: center;
    color: var(--ink-soft);
    margin-bottom: 21px;
  }

  /* Spine */
  .spine {
    position: absolute; left: 540px; top: 0; width: 42px; height: 770px;
  }
  .spine-text {
    position: absolute; left: 8px; top: 76px;
    writing-mode: vertical-rl;
    white-space: nowrap;
  }
  .spine-title {
    font-size: 28px; letter-spacing: 0.1em; text-transform: uppercase;
    line-height: 1;
  }
  .spine-author {
    display: block; margin-top: 42px;
    font-size: 19px; letter-spacing: 0.18em; line-height: 1;
  }

  /* Front cover */
  .front-cover {
    position: absolute; left: 610px; top: 0; width: 510px; height: 770px;
  }
  .front-title {
    position: absolute; top: 66px; left: 0; width: 510px;
    text-align: center; text-transform: uppercase; font-weight: 400;
    line-height: 1;
  }
  .front-title .lead {
    display: block; font-size: 40px; letter-spacing: 0.16em;
  }
  .front-title .main {
    display: block; font-size: 52px; letter-spacing: 0.14em; margin-top: 14px;
  }
  .front-title .main + .main { margin-top: 6px; }
  .cover-art {
    position: absolute; left: 140px; top: 334px; width: 215px; height: 195px;
    border-radius: 60% 45% 50% 55% / 55% 50% 55% 50%;
    background: radial-gradient(ellipse at 60% 35%, var(--pearl) 0%, var(--pearl) 40%, var(--pearl-shade) 80%, rgba(217,195,191,0.7) 100%);
  }
  .front-author {
    position: absolute; top: 680px; left: 0; width: 510px;
    text-align: center;
    font-size: 34px; letter-spacing: 0.15em; line-height: 1;
  }
</style>
</head>
<body>
  <main class="cover-wrap">
    <section class="back-cover">
      <h2 class="back-title">The Weaver's Lantern</h2>
      <div class="back-blurb">
        <p>Lorem ipsum dolor sit amet, consectetur adipiscing elit, sed do eiusmod tempor incididunt ut labore et dolore magna aliqua. Quis ipsum suspendisse ultrices gravida. Risus commodo viverra maecenas accumsan lacus vel facilisis. Lorem ipsum dolor sit amet, consectetur adipiscing elit, sed do eiusmod tempor incididunt ut labore et dolore magna aliqua. Quis ipsum suspendisse ultrices gravida. Risus commodo viverra maecenas accumsan lacus vel facilisis.</p>
        <p>Lorem ipsum dolor sit amet, consectetur adipiscing elit, sed do eiusmod tempor incididunt ut labore et dolore magna aliqua. Quis ipsum suspendisse ultrices gravida. Risus commodo viverra maecenas accumsan lacus vel facilisis. Lorem ipsum dolor sit amet, consectetur adipiscing elit, sed do eiusmod tempor incididunt ut labore et dolore magna aliqua. Quis ipsum suspendisse ultrices gravida. Risus commodo viverra maecenas accumsan lacus vel facilisis. Lorem ipsum dolor sit amet, consectetur adipiscing elit, sed do eiusmod tempor incididunt ut labore et dolore magna aliqua. Quis ipsum suspendisse ultrices gravida. Risus commodo viverra maecenas accumsan lacus vel facilisis.</p>
        <p>Lorem ipsum dolor sit amet, consectetur adipiscing elit, sed do eiusmod tempor incididunt ut labore et dolore magna aliqua. Quis ipsum suspendisse ultrices gravida. Risus commodo viverra maecenas accumsan lacus vel facilisis.</p>
      </div>
    </section>

    <section class="spine">
      <div class="spine-text">
        <span class="spine-title">The Weaver's Lantern</span>
        <span class="spine-author">Maribel Trowcastle</span>
      </div>
    </section>

    <section class="front-cover">
      <h1 class="front-title">
        <span class="lead">The</span>
        <span class="main">Weaver's</span>
        <span class="main">Lantern</span>
      </h1>
      <div class="cover-art" role="img" aria-label="Photograph of a white pearly conch shell floating on the gradient"></div>
      <p class="front-author">Maribel Trowcastle</p>
    </section>
  </main>
</body>
</html>
```